Business cards for Norwegian software consultancy business

We are in need of business cards for our Norwegian consultancy company.
“Valto Brindex AS” specializes in software development, architecture and agile methodology, providing mostly on-site services at customers.
The cards should reflect a certain level of business professionalism with an elegant touch, while paying tribute to our modern and technological heritage. Our logo should be featured, as well as room for basic information about the cardholder and legal information of the company (company name, address and VAT number).
We would like our cards to reflect that we are a modern consulting company. It should present a professional image that people will remember. The texture and color pallette should reflect our professionalism and reliability, so we prefer a light color pallette with colors such as gray, white, blue and black. The number of colors used should however not be overwhelming, with the text being distinct and readable.
We are open to untraditional layouts and playful designs as long as they communicate the intent stated above.
You could also take a look at our website http://www.brindex.no for input on our visual profile.
Our logo is attached in the form of vectors and rasterized PNG. Please comment if you would like the black-white and/or inverted versions as well.
Industry/Entity Type
Architecture
Contact Information for Business Card
Company information:
Valto Brindex AS
Kvernlia 14, 3170 Sem
482 71 519
info@brindex.no
www.brindex.no
Employee information:
Full name
Title
Email
Phone
Font styles to use
Look and feel

```html
<!DOCTYPE html>
<html lang="nb">
<head>
<meta charset="utf-8">
<title>Valto Brindex AS – Business Cards</title>
<link rel="stylesheet" href="https://fonts.googleapis.com/css2?family=Lato:wght@400;700&display=swap">
<style>
  :root {
    --bg: #cfcecd;
    --card: #f4f4f3;
    --ink: #1f1f1f;
    --blue: #4a86be;
    --divider: #c9c9c8;
  }
  * { box-sizing: border-box; margin: 0; padding: 0; }
  html, body {
    width: 1200px; height: 900px; overflow: hidden;
    background: var(--bg);
    font-family: "Lato", Arial, sans-serif;
    color: var(--ink);
  }
  .canvas { position: relative; width: 1200px; height: 900px; }
  .card {
    position: absolute; left: 330px; width: 540px; height: 300px;
    background: var(--card);
    box-shadow: 0 2px 6px rgba(0,0,0,.12);
  }
  .card--front { top: 105px; }
  .card--back  { top: 495px; }

  .edge-rule { position: absolute; right: 0; bottom: 0; width: 120px; height: 5px; background: var(--blue); }

  .brand { display: flex; align-items: center; gap: 12px; }
  .brand__square { width: 18px; height: 18px; background: var(--blue); flex: none; }
  .brand__name { font-size: 29px; font-weight: 400; letter-spacing: 3px; text-transform: uppercase; color: var(--ink); white-space: nowrap; }

  .card--front .brand { position: absolute; left: 0; right: 0; top: 0; bottom: 20px; justify-content: center; }

  .back__left { position: absolute; left: 0; top: 0; width: 270px; height: 300px; }
  .back__left .brand { position: absolute; left: 0; right: 0; top: 102px; justify-content: center; gap: 9px; }
  .back__left .brand__square { width: 14px; height: 14px; }
  .back__left .brand__name { font-size: 20px; letter-spacing: 2px; }
  .website { position: absolute; left: 0; right: 0; bottom: 58px; text-align: center; font-size: 14px; letter-spacing: 4px; }

  .back__divider { position: absolute; left: 270px; top: 20px; width: 1px; height: 260px; background: var(--divider); }

  .back__right { position: absolute; left: 322px; top: 74px; }
  .holder__name { font-size: 19px; color: var(--blue); line-height: 1.1; }
  .holder__title { font-size: 12px; text-transform: uppercase; margin-top: 3px; }
  .company { margin-top: 18px; font-size: 14px; line-height: 1.25; }
  .company__name { font-weight: 700; }
  .contacts { margin-top: 16px; list-style: none; font-size: 14px; line-height: 1.2; }
  .contacts li { display: flex; align-items: center; gap: 12px; }
  .contacts svg { width: 12px; height: 12px; fill: none; stroke: var(--blue); stroke-width: 1.4; flex: none; }
</style>
</head>
<body>
<main class="canvas">

  <section class="card card--front" aria-label="Card front">
    <div class="brand">
      <span class="brand__square"></span>
      <span class="brand__name">Valto Brindex</span>
    </div>
    <span class="edge-rule"></span>
  </section>

  <section class="card card--back" aria-label="Card back">
    <div class="back__left">
      <div class="brand">
        <span class="brand__square"></span>
        <span class="brand__name">Valto Brindex</span>
      </div>
      <p class="website">www.brindex.no</p>
    </div>

    <div class="back__divider"></div>

    <div class="back__right">
      <p class="holder__name">Eirik Dahl</p>
      <p class="holder__title">Director</p>
      <div class="company">
        <p class="company__name">Valto Brindex AS</p>
        <p>Kvernlia 14</p>
        <p>3170 Sem</p>
      </div>
      <ul class="contacts">
        <li>
          <svg viewBox="0 0 12 12" aria-hidden="true"><path d="M2 1.5l2 0 1 2.5-1.3 1a6 6 0 0 0 3.3 3.3l1-1.3 2.5 1v2a1 1 0 0 1-1 1A9 9 0 0 1 1 2.5a1 1 0 0 1 1-1z"/></svg>
          <span>482 71 519</span>
        </li>
        <li>
          <svg viewBox="0 0 12 12" aria-hidden="true"><rect x="3" y="1" width="6" height="3"/><rect x="1" y="4" width="10" height="5"/><rect x="3" y="7" width="6" height="4"/></svg>
          <span>482 71 520</span>
        </li>
        <li>
          <svg viewBox="0 0 12 12" aria-hidden="true"><rect x="1" y="2.5" width="10" height="7"/><path d="M1 2.5l5 4 5-4"/></svg>
          <span>edahl@brindex.no</span>
        </li>
      </ul>
    </div>

    <span class="edge-rule"></span>
  </section>

</main>
</body>
</html>
```